Dental Practice Website design

Design a new website for Brambleford Dental Practice.
Design should be warm, neutral in colour, with some small amount of bright colour if needed but kept to a minimum. Website should look professional, high end. Home page should be easy to navigate and simple for patients to be able to book online.
Logo in files along with some examples of websites that we like. Please ask if any further info needed.
Menu should have:
About
New Patients
Treatments
Fees
Contact Us

Industry/Entity Type

Dentistry

Number of Pages Required

4 page

Font styles to use
Sans Serif

Colors

Designer to choose colors to be used in the design.

Requirements
Must have
• Ravelle ratings badge, book online button,
Nice to have
• neutral, relaxing colours
Should not have
• harsh, bright colours!

```html
<!DOCTYPE html>
<html lang="en">
<head>
<meta charset="utf-8">
<title>Brambleford Dental Practice</title>
<link rel="stylesheet" href="https://fonts.googleapis.com/css2?family=Montserrat:wght@300;400;500;600;700&display=swap">
<style>
:root{
  --canvas:#ffffff;
  --cream:#f1f0ec;
  --mist:#e6eef8;
  --blue:#3a74b4;
  --navy:#1b2540;
  --ink:#1f2a3a;
  --muted:#6b7280;
  --line:#c9ced6;
  --black:#060606;
  --white:#ffffff;
}
*{box-sizing:border-box;margin:0;padding:0}
html,body{width:1200px;height:1200px;overflow:hidden;background:var(--canvas)}
body{font-family:"Montserrat",sans-serif;color:var(--ink)}
.stage{position:absolute;left:0;top:0;width:1932px;height:1932px;transform:scale(.62112);transform-origin:0 0}
.page{position:absolute;left:775px;top:0;width:383px;height:1932px;background:var(--cream);overflow:hidden}
.abs{position:absolute}
.photo{position:absolute}
.eyebrow{position:absolute;font-size:2.6px;color:var(--muted);display:flex;align-items:center;gap:4px}
.eyebrow svg{width:7px;height:7px}
.h2{position:absolute;font-weight:300;font-size:12.5px;line-height:14px;color:var(--ink)}
.h2 b{font-weight:600}
.copy{position:absolute;font-size:2.6px;line-height:5px;color:var(--muted)}
.link{position:absolute;font-size:3px;color:var(--ink);text-decoration:underline}
.pill{position:absolute;border-radius:8px;font-size:2.8px;display:flex;align-items:center;justify-content:center}

/* hero */
.hero{left:0;top:0;width:383px;height:198px;background:linear-gradient(100deg,#eef2f8 0%,#dbe5f1 40%,#a9bfdb 75%,#c8d6e8 100%)}
.logo{position:absolute;left:30px;top:5px;width:26px;height:18px;border:.5px solid var(--white);color:var(--white);font-size:3px;font-weight:500;display:flex;align-items:center;justify-content:center;text-align:center;line-height:3.6px}
.nav{position:absolute;left:98px;top:11px;display:flex;gap:4px;font-size:2.8px;color:var(--white)}
.phone{position:absolute;left:273px;top:11px;font-size:2.8px;color:var(--white)}
.btn-nav{left:310px;top:9px;width:43px;height:9px;background:var(--blue);color:var(--white)}
.hero-title{position:absolute;left:30px;top:90px;font-size:23.5px;line-height:23px;font-weight:300;color:var(--ink)}
.hero-title b{font-weight:600}
.chips{position:absolute;left:30px;top:155px;display:flex;gap:3px}
.chip{border:.5px solid var(--ink);border-radius:4px;font-size:2.4px;padding:1px 4px}

/* services */
.svc-band{left:0;top:453px;width:383px;height:107px;background:var(--mist)}
.svc{position:absolute;top:561px;width:90px}
.svc .photo{position:relative;height:94px}
.svc p{font-size:6px;margin-top:4px;color:var(--ink)}
.svc p span{font-size:3.5px;color:var(--muted)}
.track{left:44px;top:696px;width:218px;height:.6px;background:var(--line)}
.arrow{position:absolute;top:692px;width:10px;height:10px;border-radius:50%;border:.5px solid var(--line);background:var(--white);display:flex;align-items:center;justify-content:center}

/* effortless */
.panel{left:194px;top:792px;width:189px;height:128px;background:var(--blue);color:var(--white);padding:18px 22px}
.panel .h2,.panel .eyebrow,.panel .copy{position:static;color:var(--white)}

/* features */
.feat{position:absolute;width:70px}
.feat svg{width:10px;height:10px}
.feat h4{font-weight:400;font-size:4px;line-height:4.4px;margin-top:1px}
.feat p{font-size:2.4px;color:var(--muted);margin-top:2px}

/* pricing */
.price{position:absolute;top:1258px;width:104px;height:129px;background:var(--white);padding:14px 10px}
.price.feature{background:var(--blue);color:var(--white);box-shadow:0 2px 6px rgba(0,0,0,.15)}
.price .amt{font-size:8.5px;font-weight:400}
.price .amt small{font-size:2.6px}
.price .desc{font-size:2.4px;line-height:3.8px;color:var(--muted);margin:3px 0 4px}
.price.feature .desc,.price.feature li{color:#dbe6f3}
.price ul{list-style:none}
.price li{font-size:2.3px;color:var(--muted);display:flex;align-items:center;gap:3px;height:10px}
.price li svg{width:4px;height:4px}
.price .book{position:static;margin-top:3px;width:42px;height:8px;background:var(--blue);color:var(--white)}
.price.feature .book{background:var(--white);color:var(--blue)}

/* team */
.team-block{left:0;top:1432px;width:162px;height:148px;background:var(--navy);color:var(--white)}
.member{position:absolute;top:1523px;width:77px}
.member .photo{position:relative;height:72px}
.member .tag{height:14px;padding:3px 5px;font-size:4.5px;display:flex;justify-content:space-between;background:var(--cream)}
.member .tag small{display:block;font-size:2.2px;color:var(--muted)}
.member.active .tag{background:var(--blue);color:var(--white);margin:0 4px}
.member.active .tag small{color:#dbe6f3}
.dots{display:flex;gap:1.5px;align-items:center}
.dots i{width:3.5px;height:3.5px;border-radius:50%;background:var(--blue);display:block}
.member.active .dots i{background:var(--white)}

/* contact */
.contact-band{left:0;top:1695px;width:383px;height:120px;background:var(--mist)}
.cinfo{position:absolute;left:30px;display:flex;gap:4px;align-items:center;font-size:3px}
.cinfo i{width:10px;height:10px;border-radius:50%;background:var(--blue);display:flex;align-items:center;justify-content:center}
.cinfo i svg{width:5px;height:5px}
.cinfo small{display:block;font-size:2.4px;color:var(--muted)}
.form{left:216px;top:1647px;width:137px;height:146px;background:var(--white);padding:12px 9px}
.form h3{font-weight:400;font-size:12px;margin-bottom:6px}
.field{border:.5px solid #dde1e7;height:11px;font-size:2.4px;color:var(--muted);padding:3px 4px;margin-bottom:6px}
.row{display:flex;gap:3px}.row .field{flex:1}
.form .submit{position:static;width:100%;height:7px;background:var(--blue);color:var(--white);border-radius:4px;margin-top:4px}
.form .note{font-size:2.2px;color:var(--muted);text-align:center;margin-top:5px}

/* footer */
.footer{left:0;top:1815px;width:383px;height:117px;background:var(--black);color:var(--white)}
.fcol{position:absolute;top:25px}
.fcol h5{font-weight:300;font-size:7px;margin-bottom:5px}
.fcol li{list-style:none;font-size:2.4px;line-height:8px;color:#cfd3da}
.social{position:absolute;left:30px;top:84px;display:flex;gap:4px}
.social i{width:8px;height:8px;border-radius:50%;background:var(--blue);display:block}
.legal{position:absolute;top:108px;font-size:2.3px;color:#aab}
</style>
</head>
<body>
<div class="stage">
<main class="page">

  <!-- Hero -->
  <section class="abs hero">
    <div class="photo" role="img" aria-label="Dentist examining a smiling patient in a bright clinic" style="left:150px;top:0;width:233px;height:198px;background:linear-gradient(120deg,rgba(255,255,255,0) 0%,#c3d3e6 35%,#e4d2cf 65%,#9db5d4 100%)"></div>
    <div class="logo">BRAMBLEFORD</div>
    <nav class="nav"><span>Home</span><span>About us</span><span>Treatments</span><span>New Patients</span><span>Pricing</span><span>Contact Us</span></nav>
    <div class="phone">01632 960 418</div>
    <div class="pill btn-nav">Book Appointment</div>
    <div class="eyebrow" style="left:30px;top:80px"><svg viewBox="0 0 10 10"><path d="M5 0v10M0 5h10M1.5 1.5l7 7M8.5 1.5l-7 7" stroke="#3a74b4" stroke-width=".6"/></svg>Expert care with a gentle touch</div>
    <h1 class="hero-title">Bright Smiles,<br>Gentle <b>Care</b></h1>
    <div class="chips"><span class="chip">Checkups</span><span class="chip">Treatments</span><span class="chip">Implants</span><span class="chip">Hygiene</span><span class="chip">Braces</span></div>
    <p class="copy" style="left:30px;top:166px;width:110px;line-height:4.4px">Welcome to our friendly dental practice nestled in the heart of Brambleford. Our team of dedicated dentists is here to give you exceptional care.</p>
  </section>

  <!-- About -->
  <h2 class="h2" style="left:112px;top:239px">Where Expertise Meets<br><b>Compassion</b></h2>
  <div class="photo" role="img" aria-label="Smiling patient in the dental chair" style="left:30px;top:285px;width:148px;height:137px;background:linear-gradient(135deg,#c9b7a6,#e8ddd2 45%,#8aa7cf)"></div>
  <div class="photo" role="img" aria-label="Dentist treating a patient" style="left:107px;top:353px;width:82px;height:100px;background:linear-gradient(160deg,#e9edf2,#b9c9dc 60%,#6f8fb8)"></div>
  <div class="abs" style="left:221px;top:304px;width:112px">
    <p style="font-size:2.9px;line-height:5px;font-weight:500">Our dedicated team is committed to making your dental experience comfortable, pain-free, and rewarding.</p>
    <p class="copy" style="position:static;margin-top:4px">At our practice we believe that a visit to the dentist should be a comfortable and positive experience. We strive to create a calm and welcoming atmosphere where every patient can feel at ease and confident in the care they receive. Our team uses modern techniques and treatments to ensure your oral health is at its best.</p>
    <p class="copy" style="position:static;margin-top:4px">We are passionate about improving dental health and helping you achieve your brightest smile. Please do not hesitate to contact us with any questions or to schedule an appointment today.</p>
    <span class="link" style="position:static;display:block;margin-top:5px">Get to Know Us</span>
  </div>

  <!-- Services -->
  <div class="abs svc-band"></div>
  <div class="eyebrow" style="left:30px;top:482px"><svg viewBox="0 0 10 10"><path d="M5 0v10M0 5h10M1.5 1.5l7 7M8.5 1.5l-7 7" stroke="#3a74b4" stroke-width=".6"/></svg>Explore Our Services</div>
  <h2 class="h2" style="left:30px;top:492px">Comprehensive Care<br>for Every <b>Smile</b></h2>
  <p class="copy" style="left:243px;top:496px;width:110px;line-height:4.6px">If you're looking for an exceptional dental practice, we're here to help. Our team is made up of highly skilled professionals who are dedicated to ensuring that all our patients receive top-notch care in a welcoming setting.</p>
  <span class="link" style="left:243px;top:522px">View All Treatments</span>
  <div class="svc" style="left:30px"><div class="photo" role="img" aria-label="Dentist with patient in clinic" style="background:linear-gradient(135deg,#e7ebef,#9eb4cf 60%,#4f7fb5)"></div><p><span>01</span> General Dentistry</p></div>
  <div class="svc" style="left:125px"><div class="photo" role="img" aria-label="Close-up of white teeth with shade guide" style="background:linear-gradient(180deg,#e3c3be,#f6efe9 45%,#d8cbbd)"></div><p><span>02</span> Cosmetic Dentistry</p></div>
  <div class="svc" style="left:220px"><div class="photo" role="img" aria-label="Patient with open mouth during check" style="background:linear-gradient(135deg,#8fb5dc,#efe0d6 50%,#c8ab98)"></div><p><span>03</span> Orthodontics</p></div>
  <div class="svc" style="left:315px;width:90px"><div class="photo" role="img" aria-label="Gloved hands holding dental tools" style="background:linear-gradient(135deg,#d9e4ef,#7aa2d6 60%,#3f6fb0)"></div><p><span>04</span> Emergency Dental<br>Care</p></div>
  <div class="abs" style="left:30px;top:694px;font-size:3px;color:var(--muted)">01/06</div>
  <div class="abs track"></div>
  <div class="arrow" style="left:299px"><svg width="5" height="4" viewBox="0 0 5 4"><path d="M5 2H.5M2 .5L.5 2 2 3.5" fill="none" stroke="#1f2a3a" stroke-width=".4"/></svg></div>
  <div class="arrow" style="left:315px"><svg width="5" height="4" viewBox="0 0 5 4"><path d="M0 2h4.5M3 .5L4.5 2 3 3.5" fill="none" stroke="#1f2a3a" stroke-width=".4"/></svg></div>

  <!-- Effortless -->
  <div class="abs" style="left:0;top:742px;width:244px;height:148px;background:#e8ebef"></div>
  <div class="photo" role="img" aria-label="Smiling man receiving a dental check" style="left:0;top:742px;width:200px;height:148px;background:linear-gradient(120deg,#6a4a38,#c49a7e 40%,#f1e6df 65%,#7fa6d8)"></div>
  <div class="abs panel">
    <div class="eyebrow"><svg viewBox="0 0 10 10"><path d="M5 0v10M0 5h10M1.5 1.5l7 7M8.5 1.5l-7 7" stroke="#fff" stroke-width=".6"/></svg>Your New Visit</div>
    <h2 class="h2" style="margin-top:6px">Let's Make It<br><b>Effortless</b></h2>
    <p class="copy" style="margin-top:5px;line-height:4.4px">Our practice is always up to date with the latest techniques and technology to make sure that our patients receive the best possible results.</p>
    <p class="copy" style="margin-top:3px;line-height:4.4px">We understand that dental care can be expensive, which is why we offer affordable prices to ensure that everyone has access to quality care. Book a visit to learn more.</p>
    <div class="pill" style="position:static;margin-top:5px;width:60px;height:8px;border:.5px solid #fff;color:#fff">Book Your First Appointment</div>
  </div>

  <!-- Why choose -->
  <div class="eyebrow" style="left:30px;top:952px"><svg viewBox="0 0 10 10"><path d="M5 0v10M0 5h10M1.5 1.5l7 7M8.5 1.5l-7 7" stroke="#3a74b4" stroke-width=".6"/></svg>Why Choose Us</div>
  <h2 class="h2" style="left:30px;top:962px">Why Choose Brambleford<br>Dental <b>Practice?</b></h2>
  <p class="copy" style="left:248px;top:970px;width:100px;line-height:4.4px">Whether you need a routine examination or a more specialised treatment, we have all the resources to provide you with the best dental care possible.</p>
  <div class="abs" style="left:0;top:1002px;width:107px;height:167px;background:var(--navy)"></div>
  <div class="photo" role="img" aria-label="Close-up of a smile with dental floss" style="left:30px;top:1002px;width:136px;height:141px;background:linear-gradient(160deg,#f2e8e1,#e1c2ae 50%,#c99e85)"></div>
  <div class="feat" style="left:194px;top:1021px"><svg viewBox="0 0 10 10"><circle cx="5" cy="3" r="2" fill="none" stroke="#3a74b4" stroke-width=".5"/><path d="M1 10c0-3 2-4.5 4-4.5S9 7 9 10" fill="none" stroke="#3a74b4" stroke-width=".5"/></svg><h4>Gentle And<br>Experienced Team</h4><p>We prioritise your comfort and care</p></div>
  <div class="feat" style="left:276px;top:1021px"><svg viewBox="0 0 10 10"><path d="M3 1h4l1 4-2 4H4L2 5z" fill="none" stroke="#3a74b4" stroke-width=".5"/></svg><h4>State of the Art<br>Technology</h4><p>Modern treatments for precise results</p></div>
  <div class="feat" style="left:194px;top:1061px"><svg viewBox="0 0 10 10"><circle cx="4" cy="6" r="3" fill="none" stroke="#3a74b4" stroke-width=".5"/><circle cx="7" cy="3" r="2" fill="none" stroke="#3a74b4" stroke-width=".5"/></svg><h4>Affordable<br>Transparent Pricing</h4><p>No hidden costs, just great care</p></div>
  <div class="feat" style="left:276px;top:1061px"><svg viewBox="0 0 10 10"><rect x="2" y="1" width="6" height="8" fill="none" stroke="#3a74b4" stroke-width=".5"/><path d="M3.5 4h3M3.5 6h3" stroke="#3a74b4" stroke-width=".5"/></svg><h4>A Family Friendly<br>Environment</h4><p>Welcoming patients of all ages</p></div>
  <div class="abs" style="left:194px;top:1113px;font-size:2.5px;color:var(--muted)">Ready for a healthier, brighter smile? &nbsp;<span style="color:var(--ink);text-decoration:underline;font-size:3px">Contact us today</span></div>

  <!-- Pricing -->
  <div class="eyebrow" style="left:176px;top:1205px"><svg viewBox="0 0 10 10"><path d="M5 0v10M0 5h10M1.5 1.5l7 7M8.5 1.5l-7 7" stroke="#3a74b4" stroke-width=".6"/></svg>Our Pricing</div>
  <h2 class="h2" style="left:0;width:383px;top:1215px;text-align:center">Transparent Pricing for<br>Quality Dental <b>Care</b></h2>
  <div class="price feature" style="left:30px">
    <div class="amt">$19.99/<small>Basic Plan</small></div>
    <p class="desc">Routine checkups and cleaning for your whole family.</p>
    <ul><li><svg viewBox="0 0 4 4"><circle cx="2" cy="2" r="1.8" fill="none" stroke="#fff" stroke-width=".3"/><path d="M1.2 2l.6.6 1.1-1.2" fill="none" stroke="#fff" stroke-width=".3"/></svg>Two checkups with the dentist each year</li><li><svg viewBox="0 0 4 4"><circle cx="2" cy="2" r="1.8" fill="none" stroke="#fff" stroke-width=".3"/><path d="M1.2 2l.6.6 1.1-1.2" fill="none" stroke="#fff" stroke-width=".3"/></svg>Two hygiene visits included each year</li><li><svg viewBox="0 0 4 4"><circle cx="2" cy="2" r="1.8" fill="none" stroke="#fff" stroke-width=".3"/><path d="M1.2 2l.6.6 1.1-1.2" fill="none" stroke="#fff" stroke-width=".3"/></svg>Routine x-rays as needed</li><li><svg viewBox="0 0 4 4"><circle cx="2" cy="2" r="1.8" fill="none" stroke="#fff" stroke-width=".3"/><path d="M1.2 2l.6.6 1.1-1.2" fill="none" stroke="#fff" stroke-width=".3"/></svg>Oral cancer screening at each visit</li><li><svg viewBox="0 0 4 4"><circle cx="2" cy="2" r="1.8" fill="none" stroke="#fff" stroke-width=".3"/><path d="M1.2 2l.6.6 1.1-1.2" fill="none" stroke="#fff" stroke-width=".3"/></svg>Ten percent off other treatments</li><li><svg viewBox="0 0 4 4"><circle cx="2" cy="2" r="1.8" fill="none" stroke="#fff" stroke-width=".3"/><path d="M1.2 2l.6.6 1.1-1.2" fill="none" stroke="#fff" stroke-width=".3"/></svg>Emergency appointments when needed</li></ul>
    <div class="pill book">Book Appointment</div>
  </div>
  <div class="price" style="left:140px">
    <div class="amt">$39.99/<small>Gold Plan</small></div>
    <p class="desc">Everything in basic plus cosmetic care for a brighter smile.</p>
    <ul><li><svg viewBox="0 0 4 4"><circle cx="2" cy="2" r="1.8" fill="none" stroke="#1f2a3a" stroke-width=".3"/><path d="M1.2 2l.6.6 1.1-1.2" fill="none" stroke="#1f2a3a" stroke-width=".3"/></svg>Two checkups with the dentist each year</li><li><svg viewBox="0 0 4 4"><circle cx="2" cy="2" r="1.8" fill="none" stroke="#1f2a3a" stroke-width=".3"/><path d="M1.2 2l.6.6 1.1-1.2" fill="none" stroke="#1f2a3a" stroke-width=".3"/></svg>Three hygiene visits included each year</li><li><svg viewBox="0 0 4 4"><circle cx="2" cy="2" r="1.8" fill="none" stroke="#1f2a3a" stroke-width=".3"/><path d="M1.2 2l.6.6 1.1-1.2" fill="none" stroke="#1f2a3a" stroke-width=".3"/></svg>Routine x-rays as needed</li><li><svg viewBox="0 0 4 4"><circle cx="2" cy="2" r="1.8" fill="none" stroke="#1f2a3a" stroke-width=".3"/><path d="M1.2 2l.6.6 1.1-1.2" fill="none" stroke="#1f2a3a" stroke-width=".3"/></svg>Oral cancer screening at each visit</li><li><svg viewBox="0 0 4 4"><circle cx="2" cy="2" r="1.8" fill="none" stroke="#1f2a3a" stroke-width=".3"/><path d="M1.2 2l.6.6 1.1-1.2" fill="none" stroke="#1f2a3a" stroke-width=".3"/></svg>One whitening session per year</li><li><svg viewBox="0 0 4 4"><circle cx="2" cy="2" r="1.8" fill="none" stroke="#1f2a3a" stroke-width=".3"/><path d="M1.2 2l.6.6 1.1-1.2" fill="none" stroke="#1f2a3a" stroke-width=".3"/></svg>Fifteen percent off other treatments</li></ul>
    <div class="pill book">Book Appointment</div>
  </div>
  <div class="price" style="left:249px">
    <div class="amt">$59.99/<small>Gold Plan</small></div>
    <p class="desc">Complete cover for ongoing care and cosmetic treatment.</p>
    <ul><li><svg viewBox="0 0 4 4"><circle cx="2" cy="2" r="1.8" fill="none" stroke="#1f2a3a" stroke-width=".3"/><path d="M1.2 2l.6.6 1.1-1.2" fill="none" stroke="#1f2a3a" stroke-width=".3"/></svg>Unlimited checkups with the dentist</li><li><svg viewBox="0 0 4 4"><circle cx="2" cy="2" r="1.8" fill="none" stroke="#1f2a3a" stroke-width=".3"/><path d="M1.2 2l.6.6 1.1-1.2" fill="none" stroke="#1f2a3a" stroke-width=".3"/></svg>Four hygiene visits included each year</li><li><svg viewBox="0 0 4 4"><circle cx="2" cy="2" r="1.8" fill="none" stroke="#1f2a3a" stroke-width=".3"/><path d="M1.2 2l.6.6 1.1-1.2" fill="none" stroke="#1f2a3a" stroke-width=".3"/></svg>All x-rays included</li><li><svg viewBox="0 0 4 4"><circle cx="2" cy="2" r="1.8" fill="none" stroke="#1f2a3a" stroke-width=".3"/><path d="M1.2 2l.6.6 1.1-1.2" fill="none" stroke="#1f2a3a" stroke-width=".3"/></svg>Oral cancer screening at each visit</li><li><svg viewBox="0 0 4 4"><circle cx="2" cy="2" r="1.8" fill="none" stroke="#1f2a3a" stroke-width=".3"/><path d="M1.2 2l.6.6 1.1-1.2" fill="none" stroke="#1f2a3a" stroke-width=".3"/></svg>Two whitening sessions per year</li><li><svg viewBox="0 0 4 4"><circle cx="2" cy="2" r="1.8" fill="none" stroke="#1f2a3a" stroke-width=".3"/><path d="M1.2 2l.6.6 1.1-1.2" fill="none" stroke="#1f2a3a" stroke-width=".3"/></svg>Twenty percent off other treatments</li></ul>
    <div class="pill book">Book Appointment</div>
  </div>

  <!-- Team -->
  <div class="abs team-block">
    <div class="eyebrow" style="left:30px;top:18px;color:#c9d2e3"><svg viewBox="0 0 10 10"><path d="M5 0v10M0 5h10M1.5 1.5l7 7M8.5 1.5l-7 7" stroke="#fff" stroke-width=".6"/></svg>Our Team</div>
    <h2 class="h2" style="left:30px;top:28px;color:#fff">Meet Our Expert<br>Dental <b>Team</b></h2>
    <p class="copy" style="left:30px;top:61px;width:110px;line-height:4.4px;color:#c9d2e3">We are delighted to introduce you to our experienced and compassionate dental team. Our team comprises highly skilled dental professionals who are dedicated to providing you with quality dental care.</p>
    <div class="pill" style="left:30px;top:88px;width:38px;height:8px;border:.5px solid #fff;color:#fff">View All Experts</div>
  </div>
  <div class="member active" style="left:112px"><div class="photo" role="img" aria-label="Portrait of dentist Owen Hartley" style="background:linear-gradient(180deg,#dfe3e8,#c9a98f 55%,#8ea7c4)"></div><div class="tag"><div>Owen Hartley<small>Sr. Dental Surgeon</small></div><div class="dots"><i></i><i></i><i></i></div></div></div>
  <div class="member" style="left:194px"><div class="photo" role="img" aria-label="Portrait of dentist Clara Whitby" style="background:linear-gradient(180deg,#e6e3df,#c98a6b 50%,#d9c7b9)"></div><div class="tag"><div>Clara Whitby<small>Sr. Dental Surgeon</small></div><div class="dots"><i></i><i></i><i></i></div></div></div>
  <div class="member" style="left:276px"><div class="photo" role="img" aria-label="Portrait of dentist Megan Ashford" style="background:linear-gradient(180deg,#e4e6ea,#e0c39f 50%,#d6dde6)"></div><div class="tag"><div>Megan Ashford<small>Sr. Dental Surgeon</small></div><div class="dots"><i></i><i></i><i></i></div></div></div>

  <!-- Contact -->
  <div class="abs contact-band"></div>
  <div class="eyebrow" style="left:30px;top:1648px"><svg viewBox="0 0 10 10"><path d="M5 0v10M0 5h10M1.5 1.5l7 7M8.5 1.5l-7 7" stroke="#3a74b4" stroke-width=".6"/></svg>Let's Connect</div>
  <h2 class="h2" style="left:30px;top:1658px">Your Healthiest<br>Smile Starts <b>Here</b></h2>
  <div class="cinfo" style="top:1711px"><i><svg viewBox="0 0 10 10"><path d="M2 1l2 .5.5 2L3 4.5a6 6 0 0 0 2.5 2.5L6.5 5.5l2 .5.5 2C9 9 8 9 7 9A7 7 0 0 1 1 3c0-1 0-2 1-2z" fill="#fff"/></svg></i><div>Call Us<small>01632 960 418</small></div></div>
  <div class="cinfo" style="top:1732px"><i><svg viewBox="0 0 10 10"><rect x="1" y="2.5" width="8" height="5" fill="#fff"/><path d="M1 2.5l4 3 4-3" fill="none" stroke="#3a74b4" stroke-width=".6"/></svg></i><div>Email Us<small>hello@brambleford.example</small></div></div>
  <div class="cinfo" style="top:1753px"><i><svg viewBox="0 0 10 10"><path d="M5 9.5S2 6 2 4a3 3 0 0 1 6 0c0 2-3 5.5-3 5.5z" fill="#fff"/><circle cx="5" cy="4" r="1" fill="#3a74b4"/></svg></i><div>Location<small>12 Mill Lane, Brambleford</small></div></div>
  <form class="abs form">
    <h3>Send Message</h3>
    <div class="row"><div class="field">First Name</div><div class="field">Last Name</div></div>
    <div class="field">Email</div>
    <div class="field">Phone</div>
    <div class="field" style="height:28px">Write a Message</div>
    <div class="pill submit">Book Appointment</div>
    <p class="note">We're committed to <b>responsible</b> care and will reply<br>to you within <b>one</b> day</p>
  </form>

  <!-- Footer -->
  <footer class="abs footer">
    <div class="abs" style="left:30px;top:18px;width:36px;height:24px;border:.5px solid #fff;font-size:4.5px;display:flex;align-items:center;justify-content:center;text-align:center;line-height:5px">BRAMBLEFORD<br>DENTAL PRACTICE</div>
    <p class="copy" style="left:30px;top:50px;width:72px;line-height:5.2px;color:#cfd3da">Welcome to our friendly dental practice nestled in the heart of Brambleford. Our team of dedicated dentists is here to provide you with exceptional dental care.</p>
    <div class="social"><i></i><i></i><i></i><i></i></div>
    <div class="fcol" style="left:134px"><h5>Quick Links</h5><ul><li>Home</li><li>About us</li><li>Treatments</li><li>New Patients</li><li>Pricing</li><li>Contact Us</li></ul></div>
    <div class="fcol" style="left:210px"><h5>Treatments</h5><ul><li>General Dentistry</li><li>Cosmetic Dentistry</li><li>Orthodontics</li><li>Emergency Dental Care</li></ul></div>
    <div class="fcol" style="left:286px"><h5>Contact Us</h5><ul><li>&#9742; 01632 960 418</li><li>&#9993; hello@brambleford.example</li><li>&#9679; 12 Mill Lane, Brambleford</li></ul></div>
    <div class="legal" style="left:30px">© 2025 Brambleford Dental Practice. All rights reserved.</div>
    <div class="legal" style="left:287px">Terms &amp; Conditions · Help · Privacy Policy</div>
  </footer>

</main>
</div>
</body>
</html>
```